Upmarket Dessert Lounge needs a Business Card Design

We are an upmarket dessert lounge needing a business card to match our image.

We want something that is simple yet beautiful, feminine, classy, sophisticated and elegant. We want it to stand out and don't mind if it is bold.

The design should include our logo and colours of red or maroon with gold highlights. We don't mind if black is used.

Marlow & Quince

Target Market(s)

For those who like to indulge or treat themselves and give in to their temptations on good quality desserts.

Industry/Entity Type

Business

Requirements
Must have
• Must include our logo and our name

Marlow & Quince

M & Q

```html
<!DOCTYPE html>
<html lang="en">
<head>
<meta charset="utf-8">
<title>Marlow &amp; Quince — Business Card</title>
<link rel="stylesheet" href="https://fonts.googleapis.com/css2?family=Source+Sans+3:wght@400;600;700&display=swap">
<style>
  :root {
    --maroon: #7a1416;
    --gold: #f6dba4;
    --white: #ffffff;
    --backdrop: #b08763;
    --text-font: "Source Sans 3", "Myriad Pro", Arial, sans-serif;
  }
  * { box-sizing: border-box; margin: 0; padding: 0; }
  html, body { width: 1200px; height: 402px; overflow: hidden; }
  body { background: var(--backdrop); position: relative; font-family: var(--text-font); }

  .card {
    position: absolute;
    top: 56px;
    width: 512px;
    height: 290px;
    background: var(--maroon);
    overflow: hidden;
  }
  .card--front { left: 56px; }
  .card--back  { left: 638px; }

  .front-swoosh { position: absolute; inset: 0; width: 100%; height: 100%; }

  .brand-name {
    position: absolute;
    left: 128px;
    top: 95px;
    transform: translate(-50%, -50%);
    color: var(--maroon);
    font-weight: 600;
    font-size: 26px;
    letter-spacing: 0.5px;
    white-space: nowrap;
  }

  .details {
    position: absolute;
    right: 35px;
    color: var(--gold);
    text-align: right;
    font-size: 12.5px;
    line-height: 1.25;
  }
  .details--person { top: 44px; }
  .person-name { font-weight: 700; font-size: 16px; }
  .person-title { font-size: 12.5px; }
  .details--address { top: 104px; }

  .contact-list {
    position: absolute;
    right: 22px;
    top: 176px;
    list-style: none;
    color: var(--gold);
    font-size: 12.5px;
  }
  .contact-list li {
    display: flex;
    justify-content: flex-end;
    align-items: center;
    gap: 6px;
    height: 17.5px;
  }
  .contact-icon { width: 10px; height: 10px; flex: none; }

  .monogram {
    position: absolute;
    left: 50%;
    top: 50%;
    transform: translate(-50%, -50%);
    color: var(--gold);
    font-weight: 600;
    font-size: 92px;
    white-space: nowrap;
  }
</style>
</head>
<body>

<section class="card card--front">
  <svg class="front-swoosh" viewBox="0 0 512 290" aria-hidden="true">
    <path fill="var(--white)" d="M0 0 H262 Q336 58 306 138 Q240 232 0 264 Z"/>
    <path fill="var(--white)" d="M276 0 Q340 10 362 38 Q326 18 268 4 Z"/>
    <path fill="var(--white)" d="M0 286 Q230 262 326 154 Q258 252 0 278 Z"/>
  </svg>

  <div class="brand-name">Marlow &amp; Quince</div>

  <div class="details details--person">
    <div class="person-name">Your name</div>
    <div class="person-title">Title</div>
  </div>

  <div class="details details--address">
    <div>Street Name</div>
    <div>City Name</div>
    <div>State Zip Code</div>
  </div>

  <ul class="contact-list">
    <li>555-014-2870
      <svg class="contact-icon" viewBox="0 0 10 10" aria-hidden="true"><circle cx="5" cy="5" r="4.5" fill="var(--gold)"/><path d="M3.3 2.5 Q2.6 5.5 6.5 7.2" stroke="var(--maroon)" stroke-width="1.3" fill="none"/></svg>
    </li>
    <li>555-014-2870
      <svg class="contact-icon" viewBox="0 0 10 10" aria-hidden="true"><rect x="2.5" y="0.5" width="5" height="9" rx="1" fill="var(--gold)"/><rect x="3.5" y="2" width="3" height="3" fill="var(--maroon)"/></svg>
    </li>
    <li>hello@marlowquince.com
      <svg class="contact-icon" viewBox="0 0 10 10" aria-hidden="true"><rect x="0.5" y="2" width="9" height="6" fill="var(--gold)"/><path d="M0.5 2 L5 5.5 L9.5 2" stroke="var(--maroon)" stroke-width="0.9" fill="none"/></svg>
    </li>
    <li>www.marlowquince.com
      <svg class="contact-icon" viewBox="0 0 10 10" aria-hidden="true"><circle cx="5" cy="5" r="4.5" fill="var(--gold)"/><path d="M0.5 5 H9.5 M5 0.5 V9.5" stroke="var(--maroon)" stroke-width="0.8"/><ellipse cx="5" cy="5" rx="2" ry="4.5" stroke="var(--maroon)" stroke-width="0.8" fill="none"/></svg>
    </li>
  </ul>
</section>

<section class="card card--back">
  <div class="monogram">M &amp; Q</div>
</section>

</body>
</html>
```